Child Sponsorship Charity Needs a Wordpress Design

BrightWell GLOBAL is a not-for-profit organization that breaks the cycle of poverty through child sponsorship. We work in 7 countries around the world and are based in Canada. We currently have a Wordpress website and want to update the look and create a more engaging user experience. Our donor base is across Canada and our partners work across the globe. PLEASE SEE THE DESIGN BRIEF ATTACHED. We are looking for out site to be clean, colourful, and inviting. It should maintain our brand image, be welcoming to potential donors, and a great resource to current donors.

Project Deadline Extended Reason: Our Board of Directors wants a chance to provide feedback on the submissions and so we are extending the deadline to give them the opportunity to share their insights. Added Saturday, February 21, 2015

Charity

• Helvetica / Helvetica Neue

• Got a list of colours from the designer who made our logo:
• Brightwell Navy blue
• C: 100
• M: 80
• Y: 0
• K: 23
• Or
• R: 2
• G: 60
• B: 132
• Brightwell lighter blue
• C: 34
• M: 0
• Y: 3
• K: 0
• Or
• R: 161
• G: 221
• B: 241
• Brightwell deep red (newsletter accent colour)
• C: 0
• M: 91
• Y: 88
• K: 30
• Or
• R: 178
• G: 44
• B: 34

```html
<!DOCTYPE html>
<html lang="en">
<head>
<meta charset="utf-8">
<title>BrightWell GLOBAL – Child Sponsorship</title>
<link rel="stylesheet" href="https://fonts.googleapis.com/css2?family=Raleway:wght@400;500;600;700&family=Open+Sans:ital,wght@0,400;0,600;1,400&display=swap">
<style>
  :root {
    --navy: #023c84;
    --navy-dark: #0b2550;
    --blue: #2f7ccc;
    --blue-mid: #3a87d6;
    --blue-light: #4d9be0;
    --sky: #a1ddf1;
    --text: #333a44;
    --muted: #5a6270;
    --rule: #d9dde2;
    --page: #f5f6f7;
    --white: #ffffff;
  }
  * { box-sizing: border-box; margin: 0; padding: 0; }
  html, body { width: 1138px; height: 1200px; overflow: hidden; }
  body {
    position: relative;
    background: var(--page);
    font-family: "Open Sans", Helvetica, Arial, sans-serif;
    color: var(--text);
  }
  .abs { position: absolute; }

  /* Header */
  .brand { left: 190px; top: 38px; display: flex; align-items: center; gap: 10px; }
  .brand-dot { width: 34px; height: 34px; border-radius: 50%; background: var(--blue); }
  .brand-name { font-family: "Raleway", sans-serif; font-weight: 500; font-size: 21px; color: var(--navy-dark); letter-spacing: 0.2px; }

  .sponsor-btn {
    left: 801px; top: 25px; width: 146px; height: 32px;
    background: linear-gradient(#5aa8ea, #3f8fdc);
    color: var(--white); font-family: "Raleway", sans-serif; font-size: 14px;
    display: flex; align-items: center; justify-content: center; gap: 7px;
  }
  .sponsor-btn .ring { width: 20px; height: 20px; border: 2px solid var(--white); border-radius: 50%; }
  .search {
    left: 766px; top: 62px; width: 181px; height: 23px;
    background: var(--white); border: 1px solid #c9cdd2;
    font-size: 9.5px; font-style: italic; color: #666; padding: 0 0 0 11px;
    display: flex; align-items: center; justify-content: space-between;
  }
  .search svg { margin-right: 7px; }

  /* Navigation */
  .nav {
    left: 187px; top: 96px; width: 764px; height: 37px;
    background: linear-gradient(#3a86d6, #1f5fae);
    display: flex; align-items: center; padding-left: 28px; gap: 24.5px;
  }
  .nav a { color: var(--white); text-decoration: none; font-family: "Raleway", sans-serif; font-size: 12.8px; }

  /* Hero */
  .hero {
    left: 187px; top: 133px; width: 764px; height: 342px;
    background: linear-gradient(100deg, #6b4a33 0%, #9a7656 30%, #5b3b28 55%, #c9c4b8 80%, #7a5a40 100%);
  }
  .hero-card {
    left: 224px; top: 238px; width: 313px; height: 133px;
    background: rgba(92, 160, 222, 0.82); padding: 24px 0 0 26px;
  }
  .hero-card h1 { font-family: "Raleway", sans-serif; font-weight: 700; font-size: 28px; color: var(--white); line-height: 1; }
  .hero-card h2 { font-family: "Raleway", sans-serif; font-weight: 700; font-size: 17.5px; color: #0f3b78; margin-top: 5px; }
  .hero-card p { font-size: 8.4px; line-height: 13.5px; color: #eef5fc; margin-top: 5px; width: 270px; }
  .dots { left: 534px; top: 453px; display: flex; gap: 2px; }
  .dots span { width: 12px; height: 12px; border-radius: 50%; background: #3a2418; }

  /* About */
  .about { left: 188px; top: 508px; width: 430px; }
  .about h3 { font-family: "Raleway", sans-serif; font-weight: 400; font-size: 23px; color: #222; }
  .about .lead { font-size: 10px; line-height: 14.5px; color: #555; margin-top: 9px; }
  .about .body { font-size: 8.3px; line-height: 14.4px; color: #555; margin-top: 7px; }
  .btn-dark {
    left: 187px; top: 650px; width: 93px; height: 25px;
    background: var(--navy-dark); color: var(--white);
    font-size: 9px; font-weight: 600; display: flex; align-items: center; justify-content: center;
  }
  .video-frame {
    left: 657px; top: 500px; width: 294px; height: 181px;
    background: var(--white); border: 1px solid #dcdfe3; box-shadow: 0 1px 3px rgba(0,0,0,.12);
  }
  .video-still {
    left: 662px; top: 505px; width: 284px; height: 170px;
    background: linear-gradient(110deg, #6fb3a5 0%, #8a5a3c 45%, #6b4630 75%, #c4c9c4 100%);
  }
  .play { left: 784px; top: 570px; width: 40px; height: 40px; border-radius: 50%; background: var(--white);
    display: flex; align-items: center; justify-content: center; }

  .divider { left: 187px; top: 720px; width: 764px; height: 1px; background: var(--rule); }

  /* Blog */
  .blog-title { left: 185px; top: 747px; font-family: "Raleway", sans-serif; font-size: 19px; color: #2167b8; }
  .post { width: 180px; top: 786px; }
  .post .thumb { width: 180px; height: 99px; border: 1px solid #d2d5d9; }
  .post h4 { font-family: "Raleway", sans-serif; font-weight: 500; font-size: 12.5px; color: #222; margin-top: 12px; padding-left: 2px; }
  .post p { font-size: 8.2px; line-height: 14.3px; color: #555; margin-top: 3px; padding-left: 2px; }
  .btn-more {
    left: 186px; top: 970px; width: 133px; height: 28px;
    background: linear-gradient(#5ea9ea, #3c8bda); color: var(--white);
    font-size: 9.5px; font-weight: 600; display: flex; align-items: center; padding-left: 13px;
  }
  .btn-more .arrow { position: absolute; right: 0; top: 0; width: 22px; height: 28px; border-left: 1px solid rgba(255,255,255,.35);
    display: flex; align-items: center; justify-content: center; }

  /* Newsletter */
  .newsletter { left: 0; top: 1045px; width: 1138px; height: 73px; background: #4d99dc; }
  .news-title { left: 189px; top: 1070px; font-family: "Raleway", sans-serif; font-size: 18.5px; color: var(--white); }
  .field { top: 1073px; width: 132px; height: 24px; background: #ececec; border: 1px solid #d5d5d5;
    font-size: 8px; color: #555; display: flex; align-items: center; padding-left: 7px; }
  .btn-signup { left: 642px; top: 1073px; width: 74px; height: 24px; background: #1c4f9a; color: var(--white);
    font-size: 10.5px; font-weight: 600; display: flex; align-items: center; justify-content: center; }
  .social { left: 777px; top: 1073px; display: flex; gap: 6px; }
  .social span { width: 23px; height: 23px; border-radius: 4px; background: var(--white); }

  /* Footer */
  .footer { left: 0; top: 1118px; width: 1138px; height: 82px; background: #3a86d4; }
  .footer-links { left: 186px; top: 1140px; font-size: 10.7px; color: var(--white); }
  .footer-links span.sep { margin: 0 5px; }
  .copyright { left: 186px; top: 1161px; font-size: 8.8px; color: #e6f0fa; }
</style>
</head>
<body>

  <!-- Header -->
  <div class="abs brand">
    <span class="brand-dot"></span>
    <span class="brand-name">BrightWell GLOBAL</span>
  </div>
  <div class="abs sponsor-btn"><span class="ring"></span>Sponsor a Child</div>
  <div class="abs search">
    <span>Search here</span>
    <svg width="13" height="13" viewBox="0 0 13 13"><circle cx="5.5" cy="5.5" r="4.2" fill="none" stroke="#888" stroke-width="1.6"/><line x1="8.6" y1="8.6" x2="12" y2="12" stroke="#888" stroke-width="1.8"/></svg>
  </div>

  <nav class="abs nav">
    <a href="#">Home</a><a href="#">Sponsor a Child</a><a href="#">About Us</a><a href="#">Where we Work</a>
    <a href="#">Programs</a><a href="#">Get Involved</a><a href="#">Donate</a><a href="#">Blog</a><a href="#">Contact</a>
  </nav>

  <!-- Hero -->
  <div class="abs hero" role="img" aria-label="Photo of a young girl with hair ribbons among other children"></div>
  <div class="abs hero-card">
    <h1>SPONSOR A CHILD</h1>
    <h2>PROVDE HELP CHILDRENS</h2>
    <p>Vivamus porttitor purus nisi eleifend libero a tempus libero lectus feugiat felis Morbi diam mauris viverra in gravida mattis</p>
  </div>
  <div class="abs dots"><span></span><span></span><span></span><span></span></div>

  <!-- About -->
  <section class="abs about">
    <h3>Little About BrightWell Global</h3>
    <p class="lead">Morbi diam mauris viverra in gravida eu mattis in ante Morbi eget arcu Morbi porta libero id ullamcorper nonummy nibh ligula pulvinar metus</p>
    <p class="body">Aascetur ridiculus mus In iaculis facilisis massa Etiam eu urna Sed porta Suspendisse quam leo molestie sed uctus quis feugiat in pede Fusce tellus Sed metus augue Convallis et vehicula ut pulvinar eu ante Integer orci tellus tristique diam mauris viverra in gravida eu mattis in ante Morbi eget arcu</p>
    <p class="body" style="margin-top:4px">Mauris vel lacus vitae felis vestibulum volutpat Etiam est nunc venenatis in tristique eu imperdiet ac</p>
  </section>
  <div class="abs btn-dark">LEARN MORE</div>

  <div class="abs video-frame"></div>
  <div class="abs video-still" role="img" aria-label="Video still of smiling children"></div>
  <div class="abs play">
    <svg width="14" height="16" viewBox="0 0 14 16"><path d="M2 1 L13 8 L2 15 Z" fill="#111"/></svg>
  </div>

  <div class="abs divider"></div>

  <!-- Blog -->
  <h3 class="abs blog-title" style="font-weight:400">Recent Blog Post</h3>

  <article class="abs post" style="left:184px">
    <div class="thumb" role="img" aria-label="Photo of two boys outdoors" style="background:linear-gradient(120deg,#b7b0a6,#3b4254 55%,#8c8f99)"></div>
    <h4>Sed porta Suspendisse</h4>
    <p>Aascetur ridiculus mus In iaculis facilisis massa Etiam eu urna Sed porta Suspendiss quam leo molestie sed luctus quis</p>
  </article>
  <article class="abs post" style="left:378px">
    <div class="thumb" role="img" aria-label="Photo of a smiling boy" style="background:linear-gradient(120deg,#c98a45,#6b3e22 55%,#2c1a12)"></div>
    <h4>Curabitur vel mi sit</h4>
    <p>Aascetur ridiculus mus In iaculis facilisis massa Etiam eu urna Sed porta Suspendiss quam leo molestie sed luctus quis</p>
  </article>
  <article class="abs post" style="left:573px">
    <div class="thumb" role="img" aria-label="Photo of two young brothers in a village" style="background:linear-gradient(120deg,#d3cbbd,#9a8472 50%,#4b5a78)"></div>
    <h4>Praesent elementum</h4>
    <p>Aascetur ridiculus mus In iaculis facilisis massa Etiam eu urna Sed porta Suspendiss quam leo molestie sed luctus quis</p>
  </article>
  <article class="abs post" style="left:767px">
    <div class="thumb" role="img" aria-label="Photo of a smiling boy in a striped shirt" style="background:linear-gradient(120deg,#1a1412,#5a3a28 45%,#2a4f9c 75%,#b0323a)"></div>
    <h4>Nulla sit amet diam</h4>
    <p>Aascetur ridiculus mus In iaculis facilisis massa Etiam eu urna Sed porta Suspendiss quam leo molestie sed luctus quis</p>
  </article>

  <div class="abs btn-more">VIEW MORE BLOG
    <span class="arrow"><svg width="6" height="8" viewBox="0 0 6 8"><path d="M1 0 L5 4 L1 8 Z" fill="#fff"/></svg></span>
  </div>

  <!-- Newsletter -->
  <div class="abs newsletter"></div>
  <div class="abs news-title">Newsletter Sign Up</div>
  <div class="abs field" style="left:365px">Your name</div>
  <div class="abs field" style="left:504px">Email address</div>
  <div class="abs btn-signup">SIGN UP</div>
  <div class="abs social" aria-label="Social links">
    <span></span><span></span><span></span><span></span><span></span><span></span>
  </div>

  <!-- Footer -->
  <div class="abs footer"></div>
  <div class="abs footer-links">
    Home<span class="sep">|</span>Sponsor a Child<span class="sep">|</span>About Us<span class="sep">|</span>Where we Work<span class="sep">|</span>Programs<span class="sep">|</span>Get Involved<span class="sep">|</span>Donate<span class="sep">|</span>Blog<span class="sep">|</span>Contact
  </div>
  <div class="abs copyright">© 2015 Company Name &nbsp;All right reserved &nbsp;Term of Use</div>

</body>
</html>
```